Website offering services oriented to the metaverse and blockchain

We need an ecommerce website theme/template for a new company named Vimbral (a play on words for KORVAND the inventor of Quorvex). Vimbral will provide metaverse services such as:
• Vimbral Coin
• Vimbral wallet
• Vimbral Exchange
• Vimbral NFT
• Vimbral Tech
• Vimbral Pay
• Vimbral CaaS (community as a service)
• Vimbral CRM
• Vimbral Experience
• Vimbral Blockchain
• Vimbral Commerce
• Vimbral Space (as in outer space)
• Vimbral Art (sub of NFT)
• Vimbral Store

You can find our actual logo at the following link, in order to show us templates aligned with our brand:
https://files.brindlevault.net/share/folders/8kLmTzqWpXcVbNdRyHsEfGaUoJi2QtYxP?mode=view

Looking forward to heard back from you,

Designs look the same

We need a WordPress ecommerce website theme/template for a new company named Vimbral (a play on words for KORVAND the inventor of Quorvex). Vimbral will provide metaverse services such as: • Vimbral Coin • Vimbral wallet • Vimbral Exchange • Vimbral NFT • Vimbral Tech • Vimbral Pay • Vimbral CaaS (community as a service) • Vimbral CRM • Vimbral Experience • Vimbral Blockchain • Vimbral Commerce • Vimbral Space (as in outer space) • Vimbral Art (sub of NFT) • Vimbral Store You can find our actual logo at the following link, in order to show us templates aligned with our brand: https://files.brindlevault.net/share/folders/8kLmTzqWpXcVbNdRyHsEfGaUoJi2QtYxP?mode=view Looking forward to heard back from you,

Target Market(s)

Blockchain & Cryptocurrency Businesses

Industry/Entity Type

B2C, B2B Services.

Other font styles liked:
• Monserrat, Helvetica, Object Sans

Requirements
Nice to have
• Light background picture,
Should not have
• Arch designs

```html
<!DOCTYPE html>
<html lang="en">
<head>
<meta charset="utf-8">
<title>Vimbral</title>
<link href="https://fonts.googleapis.com/css2?family=Poppins:ital,wght@0,400;0,500;0,600;0,700;1,400&display=swap" rel="stylesheet">
<style>
:root{
  --ink:#2b2b2b;
  --brand:#2a1db8;
  --brand-light:#3d3fe0;
  --green:#1fa02c;
  --orange:#f05a0a;
  --gray-bg:#f1f2f5;
  --footer:#232325;
  --text:#3a3a3a;
  --white:#fff;
}
*{margin:0;padding:0;box-sizing:border-box}
html,body{width:1200px;height:4736px;overflow:hidden}
body{font-family:"Poppins",sans-serif;color:var(--text);background:var(--white);position:relative}
.abs{position:absolute}
.nav{position:absolute;left:0;top:0;width:1200px;height:101px;background:var(--white)}
.logo{position:absolute;left:75px;top:28px;font-size:38px;font-weight:700;color:var(--ink);letter-spacing:.5px}
.menu{position:absolute;right:75px;top:40px;display:flex;gap:33px;font-size:16px;font-weight:500;color:var(--ink)}
.menu .active{color:var(--brand)}
.hero{position:absolute;left:0;top:101px;width:1200px;height:740px;
  background:
    radial-gradient(circle at 85% 40%,rgba(120,110,255,.45),transparent 45%),
    radial-gradient(circle at 95% 85%,rgba(90,80,240,.35),transparent 40%),
    linear-gradient(120deg,#3a1fd0 0%,#2d16c4 45%,#1a0fa0 100%)}
.hero-art{position:absolute;left:83px;top:178px}
.hero-copy{position:absolute;right:72px;top:272px;text-align:right;color:var(--white)}
.hero-copy h1{font-size:82px;font-weight:700;line-height:1}
.hero-copy p{font-size:22px;line-height:37px;margin-top:22px}
.btn{display:inline-flex;align-items:center;justify-content:center;background:var(--green);color:var(--white);font-weight:600;border-radius:30px}
.hero-btn{position:absolute;right:76px;top:496px;width:180px;height:54px;font-size:18px}
h2.title{font-size:58px;font-weight:700;color:var(--ink);line-height:58px}
h2.title span{color:var(--brand)}
.welcome h2{position:absolute;left:75px;top:940px}
.welcome p{position:absolute;left:75px;top:1068px;width:575px;font-size:15px;line-height:32.5px}
.welcome .btn{position:absolute;left:75px;top:1261px;width:179px;height:55px;font-size:18px}
.welcome-art{position:absolute;left:680px;top:910px;width:450px;height:440px;
  background:
    radial-gradient(ellipse at 55% 60%,#2f6df0 0%,#4a8df5 22%,rgba(120,140,240,.75) 42%,rgba(200,208,250,.5) 62%,rgba(255,255,255,0) 75%),
    radial-gradient(circle at 25% 25%,rgba(80,90,220,.35),transparent 30%)}
.card{position:absolute;width:328px;background:var(--white);border-radius:12px;box-shadow:0 4px 18px rgba(0,0,0,.12);overflow:hidden;text-align:center}
.card .ph{height:220px}
.card h3{font-size:24px;font-weight:700;color:var(--brand);margin-top:22px}
.card p{font-size:15px;line-height:27px;margin:6px 22px 24px}
.ph-a{background:radial-gradient(circle at 75% 35%,rgba(220,80,90,.45),transparent 35%),linear-gradient(135deg,#8da2b8,#3b4b60 55%,#1c2432)}
.ph-b{background:radial-gradient(circle at 35% 45%,rgba(230,190,160,.6),transparent 35%),linear-gradient(135deg,#e5e2dc,#8f8a86 50%,#3c3a3a)}
.ph-c{background:radial-gradient(circle at 30% 55%,rgba(190,140,110,.55),transparent 35%),linear-gradient(135deg,#c9c2b7,#8c8279 50%,#4a4642)}
.courses-head{position:absolute;right:72px;top:1458px;text-align:right}
.courses-head p{font-size:15px;line-height:32.5px;width:340px;margin:40px 0 0 auto}
.courses-head .btn{margin-top:30px;width:218px;height:54px;font-size:18px}
.services-title{position:absolute;left:75px;top:2386px}
.svc{position:absolute;left:75px;width:421px;height:92px;background:var(--white);border-radius:10px;box-shadow:0 3px 14px rgba(0,0,0,.1)}
.svc svg{position:absolute;left:20px;top:18px}
.svc h4{position:absolute;left:120px;top:12px;font-size:22px;font-weight:700;color:var(--brand)}
.svc p{position:absolute;left:120px;top:44px;font-size:14px;line-height:22px;width:280px}
.services-art{position:absolute;left:524px;top:2389px;width:625px;height:423px;
  background:
    radial-gradient(ellipse at 52% 55%,#5646d8 0%,#6a5ae6 28%,rgba(140,130,240,.7) 45%,rgba(220,220,250,.6) 65%,#eeeefb 80%),
    #eeeefb;border-radius:10px}
.reviews-title{position:absolute;left:0;width:1200px;top:2928px;text-align:center}
.review{position:absolute;top:3027px;width:512px;height:215px;background:var(--white);border-radius:12px;box-shadow:0 4px 18px rgba(0,0,0,.12)}
.review p{margin:36px 25px 0;font-size:17px;font-style:italic;line-height:32.5px}
.review h5{margin:12px 25px 0;font-size:16px;font-weight:600;color:var(--brand)}
.review .bar{position:absolute;left:295px;bottom:-12px;width:200px;height:24px;background:linear-gradient(90deg,#2a4fd0,#1d6ad8);clip-path:polygon(0 0,100% 0,100% 100%,30% 100%)}
.avatar{position:absolute;top:3222px;width:88px;height:88px;border-radius:50%;border:4px solid var(--white);box-shadow:0 2px 8px rgba(0,0,0,.15)}
.av-a{background:radial-gradient(circle at 50% 40%,#d8b59b,#b58e74 35%,#e9eef3 60%)}
.av-b{background:radial-gradient(circle at 50% 40%,#8a5e45,#2d211c 40%,#eef0f2 62%)}
.blog-bg{position:absolute;left:0;top:3378px;width:1200px;height:745px;background:radial-gradient(circle at 90% 70%,rgba(80,90,240,.6),transparent 45%),linear-gradient(130deg,#2b17b8,#2a1fc6 60%,#3b3ee0)}
.blog-title{position:absolute;left:0;top:3432px;width:1200px;text-align:center;color:var(--white);font-size:58px;font-weight:700}
.post{position:absolute;top:3540px;width:328px;height:351px;background:var(--white);border-radius:6px;overflow:hidden}
.post .ph{height:193px}
.ph-d{background:radial-gradient(circle at 70% 60%,rgba(60,70,80,.7),transparent 40%),linear-gradient(135deg,#eceae6,#b9b3ab 50%,#4d4a47)}
.ph-e{background:radial-gradient(circle at 50% 50%,#bfe3ff,#4aa6f2 30%,#1f5fd6 65%,#15308f)}
.ph-f{background:radial-gradient(circle at 60% 50%,rgba(90,140,190,.6),transparent 30%),linear-gradient(135deg,#6a4a34,#2d2520 55%,#141414)}
.post h3{margin:22px 22px 0;font-size:20px;font-weight:600;line-height:31px;color:var(--ink)}
.post .go{position:absolute;right:0;bottom:0;width:51px;height:48px;background:var(--orange)}
.news-title{position:absolute;left:0;top:4168px;width:1200px;text-align:center}
.news-text{position:absolute;left:0;top:4252px;width:1200px;text-align:center;font-size:15px}
.news-input{position:absolute;left:252px;top:4301px;width:461px;height:55px;border:1px solid #bbb;border-radius:30px;font-size:15px;padding:15px 0 0 26px;color:#555}
.news-btn{position:absolute;left:728px;top:4301px;width:217px;height:55px;font-size:18px}
.footer{position:absolute;left:0;top:4417px;width:1200px;height:319px;background:var(--footer);color:#e6e6e6}
.footer .flogo{position:absolute;left:75px;top:52px;font-size:38px;font-weight:700;color:#b9b9b9}
.footer .about{position:absolute;left:75px;top:110px;width:270px;font-size:13px;line-height:25px}
.fcol{position:absolute;top:58px;font-size:13px}
.fcol h6{font-size:18px;font-weight:600;margin-bottom:14px;color:var(--white)}
.fcol li{list-style:none;line-height:32px}
.copy{position:absolute;left:75px;top:278px;font-size:13px}
.social{position:absolute;right:78px;top:277px;display:flex;gap:18px}
.social span{width:14px;height:14px;border-radius:50%;background:#e6e6e6}
</style>
</head>
<body>

<header class="nav">
  <div class="logo">Vimbral</div>
  <nav class="menu"><span class="active">Home</span><span>About Us</span><span>Courses</span><span>Services</span><span>Blog</span><span>Reviews</span><span>Contact Us</span></nav>
</header>

<section class="hero">
  <div class="hero-copy" style="top:171px">
    <h1>Vimbral</h1>
    <p>We are dedicated to educating and certifying<br>people and companies in the cryptocurrency,<br>blockchain and related fields</p>
  </div>
  <a class="btn hero-btn" style="top:395px">Read More</a>
</section>
<svg class="hero-art" width="520" height="660" viewBox="0 0 520 660" role="img" aria-label="Illustration of a woman at a laptop surrounded by finance and security icons">
  <defs>
    <radialGradient id="blob" cx="50%" cy="42%" r="60%">
      <stop offset="0" stop-color="#a6d4f6"/>
      <stop offset="0.55" stop-color="#80bcef"/>
      <stop offset="1" stop-color="#5e9fe6"/>
    </radialGradient>
    <radialGradient id="glow" cx="50%" cy="58%" r="35%">
      <stop offset="0" stop-color="#ffffff" stop-opacity=".45"/>
      <stop offset="1" stop-color="#ffffff" stop-opacity="0"/>
    </radialGradient>
  </defs>
  <path d="M250 2 C360 -6 470 40 500 150 C530 260 500 360 470 440 C440 530 380 640 280 656 C180 670 90 610 40 520 C-6 430 -10 330 20 240 C50 140 130 10 250 2 Z" fill="url(#blob)"/>
  <path d="M250 2 C360 -6 470 40 500 150 C530 260 500 360 470 440 C440 530 380 640 280 656 C180 670 90 610 40 520 C-6 430 -10 330 20 240 C50 140 130 10 250 2 Z" fill="url(#glow)"/>
</svg>
<svg class="abs" style="left:0;top:690px" width="1200" height="160" viewBox="0 0 1200 160">
  <path d="M0 8 C120 80 230 148 380 146 C560 142 760 20 920 24 C1040 28 1130 110 1200 146 L1200 160 L0 160 Z" fill="#fff"/>
</svg>

<section class="welcome">
  <h2 class="title">Welcome to<br><span>Vimbral</span></h2>
  <p>Sed ut perspiciatis unde omnis iste natus error sit voluptatem accusantium doloremque laudantium, totam rem aperiam, eaque ipsa quae ab illo inventore veritatis et quasi architecto beatae vitae dicta sunt explicabo. Nemo enim ipsam voluptatem quia voluptas sit aspernatur aut odit aut fugit, sed quia consequuntur magni dolores.</p>
  <a class="btn">Read More</a>
  <div class="welcome-art" role="img" aria-label="Isometric illustration of blockchain servers and data blocks"></div>
</section>

<section class="courses">
  <article class="card" style="left:75px;top:1426px"><div class="ph ph-a" role="img" aria-label="Photo of two men studying trading charts"></div><h3>Sed Perspiciatis</h3><p>Nemo enim ipsam voluptatem quia voluptas sit aspernatur aut.</p></article>
  <article class="card" style="left:419px;top:1612px"><div class="ph ph-b" role="img" aria-label="Photo of colleagues reviewing charts on a laptop"></div><h3>Sed Perspiciatis</h3><p>Nemo enim ipsam voluptatem quia voluptas sit aspernatur aut.</p></article>
  <article class="card" style="left:75px;top:1796px"><div class="ph ph-c" role="img" aria-label="Photo of a woman working on a laptop"></div><h3>Sed Perspiciatis</h3><p>Nemo enim ipsam voluptatem quia voluptas sit aspernatur aut.</p></article>
  <div class="courses-head">
    <h2 class="title">Cryptocurrency<br><span>Certification<br>Courses</span></h2>
    <p>Sed ut perspiciatis unde omnis iste natus error sit voluptatem accusantium doloremque laudantium,totam rem aperiam, eaque ipsa quae ab illo inventore veritatis et quasi architecto.</p>
    <a class="btn">View All Courses</a>
  </div>
</section>

<svg class="abs" style="left:0;top:2140px" width="1200" height="748" viewBox="0 0 1200 748">
  <path d="M6 40 C120 90 240 150 420 150 C620 150 820 40 1000 34 C1100 30 1160 60 1200 80 L1200 746 L6 746 Z" fill="#f1f2f5"/>
</svg>
<section class="services">
  <h2 class="title services-title">Our <span>Services</span></h2>
  <div class="svc" style="top:2478px">
    <svg width="80" height="56" viewBox="0 0 80 56" fill="none" stroke="#2a1db8" stroke-width="2.4"><rect x="4" y="6" width="68" height="44" rx="3"/><line x1="14" y1="18" x2="60" y2="18"/><line x1="14" y1="27" x2="48" y2="27"/><circle cx="54" cy="38" r="7"/></svg>
    <h4>Perspiciatis</h4><p>Nemo enim ipsam voluptatem quia voluptas sit aspernatur aut.</p>
  </div>
  <div class="svc" style="top:2588px">
    <svg width="80" height="56" viewBox="0 0 80 56" fill="none" stroke="#2a1db8" stroke-width="2.4"><circle cx="38" cy="28" r="24"/><circle cx="38" cy="28" r="14"/><path d="M6 28h14l5-9 6 18 5-9h26"/></svg>
    <h4>Perspiciatis</h4><p>Nemo enim ipsam voluptatem quia voluptas sit aspernatur aut.</p>
  </div>
  <div class="svc" style="top:2698px">
    <svg width="80" height="56" viewBox="0 0 80 56" fill="none" stroke="#2a1db8" stroke-width="2.4"><rect x="10" y="4" width="44" height="28" rx="2"/><circle cx="16" cy="44" r="5"/><circle cx="36" cy="44" r="5"/><circle cx="56" cy="44" r="5"/><path d="M8 55c2-5 14-5 16 0M28 55c2-5 14-5 16 0M48 55c2-5 14-5 16 0"/></svg>
    <h4>Perspiciatis</h4><p>Nemo enim ipsam voluptatem quia voluptas sit aspernatur aut.</p>
  </div>
  <div class="services-art" role="img" aria-label="Illustration of people around a large dashboard with coin icons"></div>
</section>

<section class="reviews">
  <h2 class="title reviews-title">Our <span>Reviews</span></h2>
  <div class="review" style="left:75px"><p>“ Sed ut perspiciatis unde omnis iste natus error sit voluptatem accusantium doloremque laudanti, totam rem aperiam, eaque ipsa...”</p><h5>Name Heading</h5><div class="bar"></div></div>
  <div class="review" style="left:626px"><p>“ Sed ut perspiciatis unde omnis iste natus error sit voluptatem accusantium doloremque laudanti, totam rem aperiam, eaque ipsa...”</p><h5>Name Heading</h5><div class="bar"></div></div>
  <div class="avatar av-a" style="left:107px" role="img" aria-label="Reviewer portrait"></div>
  <div class="avatar av-b" style="left:649px" role="img" aria-label="Reviewer portrait"></div>
</section>

<section class="blog">
  <div class="blog-bg"></div>
  <svg class="abs" style="left:0;top:3960px" width="1200" height="165" viewBox="0 0 1200 165">
    <path d="M0 160 C300 130 700 120 1000 70 C1100 52 1160 30 1200 0 L1200 165 L0 165 Z" fill="#fff"/>
  </svg>
  <h2 class="blog-title">Blog Posts</h2>
  <article class="post" style="left:75px"><div class="ph ph-d" role="img" aria-label="Photo of a man analysing a trading chart on a laptop"></div><h3>Sed ut perspiciatis unde omnis iste natus error voluptatem.</h3><div class="go"><svg width="51" height="48" viewBox="0 0 51 48"><path d="M22 16l8 8-8 8" stroke="#fff" stroke-width="3" fill="none"/></svg></div></article>
  <article class="post" style="left:436px"><div class="ph ph-e" role="img" aria-label="Isometric illustration of a blue digital city"></div><h3>Sed ut perspiciatis unde omnis iste natus error voluptatem.</h3><div class="go"><svg width="51" height="48" viewBox="0 0 51 48"><path d="M22 16l8 8-8 8" stroke="#fff" stroke-width="3" fill="none"/></svg></div></article>
  <article class="post" style="left:797px"><div class="ph ph-f" role="img" aria-label="Photo of a man at a desk with trading monitors"></div><h3>Sed ut perspiciatis unde omnis iste natus error voluptatem.</h3><div class="go"><svg width="51" height="48" viewBox="0 0 51 48"><path d="M22 16l8 8-8 8" stroke="#fff" stroke-width="3" fill="none"/></svg></div></article>
</section>

<section class="newsletter">
  <h2 class="title news-title">Newsletter <span>Sign Up</span></h2>
  <p class="news-text">Sed ut perspiciatis unde omnis iste natus error sit.</p>
  <div class="news-input">Enter Email Address</div>
  <a class="btn news-btn">Subscribe Now</a>
</section>

<footer class="footer">
  <div class="flogo">Vimbral</div>
  <p class="about">Sed ut perspiciatis unde omnis iste natus error sit voluptatem acc usantium doloremque</p>
  <div class="fcol" style="left:360px"><h6>Site Map</h6><ul><li>Home</li><li>About Us</li><li>Courses</li><li>Services</li></ul></div>
  <div class="fcol" style="left:472px;top:90px"><ul><li>Blog</li><li>Reviews</li><li>Contact Us</li></ul></div>
  <div class="fcol" style="left:654px"><h6>Resources</h6><ul><li>Sed ut perspiciatis</li><li>Unde omnis</li><li>atus error sit voluptatem</li><li>Accusantiumolore</li></ul></div>
  <div class="fcol" style="left:902px"><h6>Support</h6><ul><li>Sed ut perspiciatis</li><li>Unde omnis</li><li>atus error sit voluptatem</li><li>Accusantiumolore</li></ul></div>
  <p class="copy">Copyright © 2021. Company Name All Right Reserved</p>
  <div class="social"><span></span><span></span><span></span><span></span><span></span><span></span></div>
</footer>

</body>
</html>
```